Stylish Business Cards Wanted

- DOUBLE SIDED Design Required -

High end, edgy cards for a corporate and personal stylist. Must include logo,
Name: Belinda Harwick
Title: Director and Stylist
telephone : +61 8 7142 5809
email: belinda@theloombriefing.example
website: theloombriefing.example
Tag: Corporate Workwear & Uniform Specialist | Personal Stylist
Would like nice icons for telephone, email, website

Target Market(s)

Businesses wanting stylish uniforms, people wanting stylish wardrobes

Industry/Entity Type

Corporate Workwear Stylist

Contact Information for Business Card

I would like black, white and gold foiling incorporated in the design - possibly a touch of the other colours on my branding guide attached Name: Belinda Harwick Title: Director and Stylist telephone : +61 8 7142 5809 email: belinda@theloombriefing.example website: theloombriefing.example Tag: Corporate Workwear & Uniform Specialist | Personal Stylist Would like nice icons for telephone, email, website

Font styles to use
Other font styles liked:
• Raleway

Colors

Designer to choose colors to be used in the design.

Requirements
Must have
• Gold foil accents

```html
<!DOCTYPE html>
<html lang="en">
<head>
<meta charset="utf-8">
<title>The Loom Briefing — Business Cards</title>
<link rel="stylesheet" href="https://fonts.googleapis.com/css2?family=Roboto:wght@400;500&family=Yellowtail&display=swap">
<style>
  :root {
    --backdrop: #cfcfcf;
    --navy: #141b2e;
    --gold: #e2b553;
    --white: #ffffff;
    --pink: #d3156a;
    --script: "Yellowtail", cursive;
    --sans: "Roboto", Arial, sans-serif;
  }
  * { margin: 0; padding: 0; box-sizing: border-box; }
  html, body { width: 1200px; height: 852px; overflow: hidden; }
  body { background: var(--backdrop); position: relative; font-family: var(--sans); }

  .card {
    position: absolute;
    width: 520px; height: 300px;
    border-radius: 26px;
    background: var(--navy);
    overflow: hidden;
    top: 276px;
  }
  .card--front { left: 60px; }
  .card--back { left: 620px; }

  .brand-name {
    font-family: var(--sans);
    font-weight: 500;
    text-transform: uppercase;
    letter-spacing: 4px;
    white-space: nowrap;
  }
  .card--front .brand-name {
    position: absolute; left: 0; right: 0; top: 132px;
    text-align: center; font-size: 30px; color: var(--gold);
  }

  .card__waves { position: absolute; inset: 0; width: 100%; height: 100%; }

  .card--back .brand-name {
    position: absolute; right: 36px; top: 58px;
    font-size: 20px; color: var(--white); letter-spacing: 3px;
  }

  .holder { position: absolute; left: 40px; top: 82px; }
  .holder__name { font-family: var(--script); font-weight: 400; font-size: 34px; color: var(--gold); line-height: 1; }
  .holder__title { font-size: 13px; color: var(--white); margin-top: 4px; }

  .contacts { position: absolute; left: 40px; top: 148px; list-style: none; }
  .contacts li {
    display: flex; align-items: center; gap: 10px;
    font-size: 13px; color: var(--white); height: 21px; white-space: nowrap;
  }
  .contacts svg { width: 13px; height: 13px; flex: none; }
  .social-mark { width: 13px; height: 13px; background: var(--gold); border-radius: 2px; flex: none; }

  .tagline {
    position: absolute; right: 34px; bottom: 44px;
    font-family: var(--script); font-size: 15px; color: var(--navy);
    text-align: right; line-height: 1.25;
  }
</style>
</head>
<body>

  <section class="card card--front" aria-label="Card front">
    <p class="brand-name">The Loom Briefing</p>
  </section>

  <section class="card card--back" aria-label="Card back">
    <svg class="card__waves" viewBox="0 0 520 300" preserveAspectRatio="none" aria-hidden="true">
      <path d="M0,300 L0,286 C160,284 255,272 310,215 C355,160 425,128 520,122 L520,300 Z" fill="var(--gold)"/>
      <path d="M50,293 C185,291 270,272 325,222 C370,172 435,142 520,136 L520,150 C445,154 385,180 342,228 C285,284 190,298 50,293 Z" fill="var(--navy)"/>
      <path d="M70,299 C200,297 290,280 350,236 C395,196 450,172 520,168" fill="none" stroke="var(--navy)" stroke-width="4"/>
      <path d="M0,102 A16,38 0 0 1 0,178 Z" fill="var(--pink)"/>
    </svg>

    <p class="brand-name">The Loom Briefing</p>

    <div class="holder">
      <h1 class="holder__name">Belinda Harwick</h1>
      <p class="holder__title">Director and Stylist</p>
    </div>

    <ul class="contacts">
      <li><span class="social-mark"></span>/theloombriefing101</li>
      <li>
        <svg viewBox="0 0 16 16"><path d="M4 1.5 6.5 5 5 6.5c.8 1.8 2.7 3.7 4.5 4.5L11 9.5l3.5 2.5-1.2 2.5C8 14.5 1.5 8 1.5 2.7Z" fill="none" stroke="var(--gold)" stroke-width="1.3"/></svg>
        +61 8 7142 5809
      </li>
      <li>
        <svg viewBox="0 0 16 16"><rect x="1.5" y="3.5" width="13" height="9" fill="none" stroke="var(--gold)" stroke-width="1.3"/><path d="M1.5 3.5 8 9l6.5-5.5" fill="none" stroke="var(--gold)" stroke-width="1.3"/></svg>
        belinda@theloombriefing.example
      </li>
      <li>
        <svg viewBox="0 0 16 16"><circle cx="8" cy="8" r="6.5" fill="none" stroke="var(--gold)" stroke-width="1.3"/><path d="M1.5 8h13M8 1.5c-3 3.5-3 9.5 0 13M8 1.5c3 3.5 3 9.5 0 13" fill="none" stroke="var(--gold)" stroke-width="1.1"/></svg>
        theloombriefing.example
      </li>
    </ul>

    <p class="tagline">Personal Stylist<br>Corporate Workwear<br>and Uniform Specialist</p>
  </section>

</body>
</html>
```